Weightloss company needs Business Card

We want a business card that is clean and professional, yet portrays that we are a friendly, innovative, and versatile program designed to fit the needs of our clients.
I would like there to be 2 sides, one side having an appointment card, and the other side containing the logo and business information. There can be decorations on both sides. The logo is attached.

Target Market(s)

Men and women 40-60

Industry/Entity Type

Business

Contact Information for Business Card

Font styles to use
Sans Serif

Requirements
Must have
• The logo, space for business information
Nice to have
• The colors in the logo
Should not have
• No pictures of people or food

```html
<!DOCTYPE html>
<html lang="en">
<head>
<meta charset="utf-8">
<title>Uplift Wellness – Business Card</title>
<link rel="stylesheet" href="https://fonts.googleapis.com/css2?family=Source+Sans+3:ital,wght@0,400;0,600;0,700;1,400;1,700&display=swap">
<style>
  :root {
    --brand-red: #e8163f;
    --brand-cyan: #2dd2f0;
    --text-grey: #555a5e;
    --rule-grey: #6d6f72;
    --card-white: #ffffff;
    --card-tint: #d9f6fc;
    --backdrop: #4a4a4a;
  }
  * { margin: 0; padding: 0; box-sizing: border-box; }
  html, body {
    width: 1105px; height: 1200px; overflow: hidden;
    background: var(--backdrop);
    font-family: "Source Sans 3", sans-serif;
  }
  .card {
    position: absolute; left: 196px; width: 720px; height: 412px;
    border-radius: 22px; overflow: hidden;
  }
  .card--front { top: 146px; background: var(--card-white); }
  .card--back { top: 602px; background: var(--card-tint); }

  .brand-mark {
    position: absolute; display: flex; align-items: center; gap: 10px;
    color: var(--brand-red); font-weight: 700; line-height: 1;
  }
  .brand-mark__dot { width: 14px; height: 14px; border-radius: 50%; background: var(--brand-red); flex: none; }
  .card--front .brand-mark { left: 70px; top: 164px; font-size: 40px; }
  .card--back .brand-mark { right: 48px; top: 62px; font-size: 30px; }

  .divider {
    position: absolute; left: 380px; top: 68px; width: 1px; height: 240px;
    background: #b9bcbf;
  }
  .contact { position: absolute; left: 417px; top: 68px; color: var(--text-grey); }
  .contact__name { color: var(--brand-red); font-size: 27px; font-weight: 600; letter-spacing: 0.5px; line-height: 1.1; }
  .contact__title { color: var(--brand-cyan); font-size: 19px; line-height: 1.3; margin-bottom: 10px; }
  .contact__address { font-size: 19px; line-height: 26px; margin-bottom: 6px; }
  .contact__list { list-style: none; }
  .contact__item { display: flex; align-items: center; gap: 10px; font-size: 19px; line-height: 28px; }
  .contact__icon { width: 18px; height: 18px; flex: none; fill: var(--brand-red); }

  .wave { position: absolute; left: 0; top: 0; width: 720px; height: 412px; }
  .website {
    position: absolute; left: 25px; top: 360px; color: #fff;
    font-size: 18px; font-weight: 700; font-style: italic; letter-spacing: 1.5px;
  }

  .appointment__title {
    position: absolute; left: 50px; top: 56px;
    color: var(--brand-red); font-size: 27px; font-weight: 700;
  }
  .appointment__row { position: absolute; left: 0; width: 720px; height: 30px; color: var(--text-grey); font-size: 20px; }
  .appointment__label { position: absolute; top: 0; }
  .appointment__line { position: absolute; top: 20px; height: 1px; background: var(--rule-grey); }
  .label-date { left: 54px; }
  .line-date { left: 116px; width: 254px; }
  .label-time { left: 387px; }
  .line-time { left: 447px; width: 137px; }
  .label-ampm { left: 594px; }
  .appointment__note {
    position: absolute; left: 0; width: 720px; top: 356px; text-align: center;
    color: var(--text-grey); font-size: 16.5px; font-style: italic;
  }
</style>
</head>
<body>

<section class="card card--front" aria-label="Business card front">
  <svg class="wave" viewBox="0 0 720 412" aria-hidden="true">
    <path d="M0 312 C 160 300, 280 380, 420 376 C 540 372, 640 330, 720 320 L720 412 L0 412 Z" fill="var(--brand-cyan)"/>
    <path d="M0 326 C 160 318, 280 396, 410 390 C 540 386, 640 340, 720 324 L720 412 L0 412 Z" fill="var(--card-white)"/>
    <path d="M0 332 C 160 326, 280 404, 410 398 C 540 394, 640 348, 720 330 L720 412 L0 412 Z" fill="var(--brand-red)"/>
  </svg>

  <div class="brand-mark">
    <span class="brand-mark__name">Uplift Wellness</span>
    <span class="brand-mark__dot"></span>
  </div>

  <div class="divider"></div>

  <div class="contact">
    <p class="contact__name">MARK DALTON</p>
    <p class="contact__title">CEO/FOUNDER</p>
    <p class="contact__address">4120 Willow Court<br>Juneau, Alaska 99801</p>
    <ul class="contact__list">
      <li class="contact__item">
        <svg class="contact__icon" viewBox="0 0 24 24"><path d="M6.6 10.8a15.1 15.1 0 0 0 6.6 6.6l2.2-2.2a1 1 0 0 1 1-.25 11.4 11.4 0 0 0 3.6.57 1 1 0 0 1 1 1V20a1 1 0 0 1-1 1A17 17 0 0 1 3 4a1 1 0 0 1 1-1h3.5a1 1 0 0 1 1 1c0 1.25.2 2.45.57 3.57a1 1 0 0 1-.25 1z"/></svg>
        <span>555 210 4836</span>
      </li>
      <li class="contact__item">
        <svg class="contact__icon" viewBox="0 0 24 24"><path d="M7 1h10a2 2 0 0 1 2 2v18a2 2 0 0 1-2 2H7a2 2 0 0 1-2-2V3a2 2 0 0 1 2-2zm0 3v14h10V4z"/></svg>
        <span>555 783 1902</span>
      </li>
      <li class="contact__item">
        <svg class="contact__icon" viewBox="0 0 24 24"><path d="M6 2h12v6H6zM3 9h18a1 1 0 0 1 1 1v8h-4v4H6v-4H2v-8a1 1 0 0 1 1-1zm5 7v4h8v-4z"/></svg>
        <span>555 346 7051</span>
      </li>
      <li class="contact__item">
        <svg class="contact__icon" viewBox="0 0 24 24"><path d="M2 5h20v14H2zm2 2v.5l8 5 8-5V7l-8 5z"/></svg>
        <span>hello@upliftwell.com</span>
      </li>
    </ul>
  </div>

  <p class="website">www.upliftwell.com</p>
</section>

<section class="card card--back" aria-label="Appointment card back">
  <h2 class="appointment__title">Next Appointment</h2>

  <div class="brand-mark">
    <span class="brand-mark__name">Uplift Wellness</span>
    <span class="brand-mark__dot"></span>
  </div>

  <div class="appointment__row" style="top:164px">
    <span class="appointment__label label-date">Date</span><span class="appointment__line line-date"></span>
    <span class="appointment__label label-time">Time</span><span class="appointment__line line-time"></span>
    <span class="appointment__label label-ampm">am/pm</span>
  </div>
  <div class="appointment__row" style="top:236px">
    <span class="appointment__label label-date">Date</span><span class="appointment__line line-date"></span>
    <span class="appointment__label label-time">Time</span><span class="appointment__line line-time"></span>
    <span class="appointment__label label-ampm">am/pm</span>
  </div>
  <div class="appointment__row" style="top:302px">
    <span class="appointment__label label-date">Date</span><span class="appointment__line line-date"></span>
    <span class="appointment__label label-time">Time</span><span class="appointment__line line-time"></span>
    <span class="appointment__label label-ampm">am/pm</span>
  </div>

  <p class="appointment__note">Please give 24 hours notice cancelling your appointment or a fee may be charged</p>
</section>

</body>
</html>
```